New Business Card Design for Manufacturing

We are an engineering/manufacturing company that offers Advanced machining/assembly/engineering services, as well as innovative products for the heavy duty engine cooling markets.

We are looking to get a new business card designed that is clean and modern looking, but still fits the wide range of technical/skilled work we do.

- We hope to use this design as the base for other design work in new Presentations, web, and print work.

Industry/Entity Type

Engineering

Contact Information for Business Card

Our preferred color of blue is (RGB) 22/71/159 but can vary slightly from that color. Our content will be our Logo and full company name (Vantrell Forge Works, Inc.), company address, name, job title, phone number with extension, cell number, fax number, website, and email address on the cards.
We'd like the full company name next to the logo, but we are open to other interpretations of that layout.
Preferably, we would like the back side to be clean with just our logo, and the front to contain all of the contact information.

Colors
2f74b4
0355a3
85abd2

Requirements
Must have
• - Logo, company name, needed content - We are open to interpretation beyond that.
• - Standard size business card.
• - Horizontal orientation.
• - Enough space for lengthy names / job titles (for example, a job title could read "Directory of Human Resources" or "V.P. of Governmental Affairs"). We need this to look clean, whether the title be short (CEO) or long (as described above).

```html
<!DOCTYPE html>
<html lang="en">
<head>
<meta charset="utf-8">
<title>Vantrell Forge Works – Business Card</title>
<link rel="stylesheet" href="https://fonts.googleapis.com/css2?family=Roboto:wght@400;500&family=Roboto+Condensed:wght@500;700&display=swap">
<style>
  :root {
    --brand-blue: #0f54a3;
    --card-white: #f7f7f7;
    --card-grey: #7c848b;
    --text-dark: #4a4f55;
    --tagline-grey: #5d6a78;
    --backdrop: #e8e5e1;
  }
  * { margin: 0; padding: 0; box-sizing: border-box; }
  html, body { width: 1200px; height: 960px; overflow: hidden; }
  body {
    position: relative;
    background: var(--backdrop);
    font-family: "Roboto", Arial, sans-serif;
  }
  .card {
    position: absolute;
    width: 600px;
    height: 343px;
    border-radius: 20px;
    overflow: hidden;
    box-shadow: 0 3px 8px rgba(0,0,0,0.25);
  }
  .card-front { left: 302px; top: 128px; background: var(--card-white); }
  .card-back { left: 298px; top: 488px; background: var(--card-grey); }

  .name-band { position: absolute; left: 0; top: 58px; }
  .person { position: absolute; left: 41px; top: 68px; color: #fff; }
  .person-name {
    font-family: "Roboto Condensed", Arial, sans-serif;
    font-weight: 500; font-size: 25px; line-height: 28px;
  }
  .person-title { font-size: 14.5px; line-height: 20px; }

  .wordmark {
    font-family: "Roboto Condensed", Arial, sans-serif;
    font-weight: 700; text-transform: uppercase; letter-spacing: 0.5px;
  }
  .front-wordmark {
    position: absolute; left: 330px; top: 58px;
    font-size: 54px; line-height: 62px; color: var(--brand-blue);
  }
  .tagline {
    position: absolute;
    font-family: "Roboto Condensed", Arial, sans-serif;
    font-weight: 700; text-transform: uppercase; font-size: 14px; letter-spacing: 0.3px;
  }
  .front-tagline { left: 325px; top: 124px; color: var(--tagline-grey); }

  .contact-list {
    position: absolute; left: 42px; top: 226px; list-style: none;
    font-size: 14.5px; color: var(--text-dark); line-height: 19px;
  }
  .contact-list li { display: flex; align-items: center; gap: 8px; }
  .contact-list svg { width: 13px; height: 13px; fill: var(--brand-blue); flex: none; }

  .address {
    position: absolute; right: 52px; top: 257px; text-align: right;
    font-size: 14.5px; line-height: 19px; color: var(--text-dark); font-style: normal;
  }

  .back-lockup { position: absolute; left: 108px; top: 128px; display: flex; align-items: flex-start; gap: 22px; color: #fff; }
  .back-wordmark { font-size: 56px; line-height: 64px; }
  .company-name {
    font-family: "Roboto Condensed", Arial, sans-serif; font-weight: 700;
    text-transform: uppercase; font-size: 19px; line-height: 19px; margin-top: 6px;
  }
  .back-tagline { left: 108px; top: 195px; color: #fff; }
</style>
</head>
<body>
  <section class="card card-front" aria-label="Business card front">
    <svg class="name-band" width="330" height="62" viewBox="0 0 330 62" aria-hidden="true">
      <polygon points="0,0 330,0 318,62 0,62" fill="var(--brand-blue)"/>
    </svg>
    <div class="person">
      <p class="person-name">DORIAN KELLAWAY</p>
      <p class="person-title">V.P. of Governmental Affairs</p>
    </div>
    <p class="wordmark front-wordmark">Vantrell</p>
    <p class="tagline front-tagline">Built to Endure</p>

    <ul class="contact-list">
      <li><svg viewBox="0 0 24 24"><path d="M6.6 10.8c1.4 2.8 3.8 5.1 6.6 6.6l2.2-2.2c.3-.3.7-.4 1-.2 1.1.4 2.3.6 3.6.6.6 0 1 .4 1 1V20c0 .6-.4 1-1 1C10.6 21 3 13.4 3 4c0-.6.4-1 1-1h3.5c.6 0 1 .4 1 1 0 1.3.2 2.5.6 3.6.1.3 0 .7-.2 1z"/></svg>614 302 7815</li>
      <li><svg viewBox="0 0 24 24"><path d="M7 1h10a2 2 0 0 1 2 2v18a2 2 0 0 1-2 2H7a2 2 0 0 1-2-2V3a2 2 0 0 1 2-2zm0 3v14h10V4zm5 15.5a1 1 0 1 0 0 2 1 1 0 0 0 0-2z"/></svg>614 559 2047</li>
      <li><svg viewBox="0 0 24 24"><path d="M2 5h20v14H2zm2 2v.5l8 5 8-5V7l-8 5z"/></svg>dorian@vantrell.com</li>
      <li><svg viewBox="0 0 24 24"><path d="M12 2a10 10 0 1 0 0 20 10 10 0 0 0 0-20zm-1 17.9A8 8 0 0 1 4.2 10L9 14.8v1a2 2 0 0 0 2 2zm6.9-2.5A2 2 0 0 0 16 16h-1v-3a1 1 0 0 0-1-1H8v-2h2a1 1 0 0 0 1-1V7h2a2 2 0 0 0 2-2v-.4a8 8 0 0 1 2.9 12.8z"/></svg>www.vantrell.com</li>
    </ul>

    <address class="address">4120 Larkspur Road<br>Fairbanks, Alaska 99712</address>
  </section>

  <section class="card card-back" aria-label="Business card back">
    <div class="back-lockup">
      <p class="wordmark back-wordmark">Vantrell</p>
      <p class="company-name">Vantrell<br>Forge<br>Works, Inc.</p>
    </div>
    <p class="tagline back-tagline">Built to Endure</p>
  </section>
</body>
</html>
```